4th Generation Family Business Needs a New Card Design!

We are a family owned 4th Generation company. We are based in the Sydney, Australia area and we are desperately in need of a more modern and classy card. We are monumental masons who design, supply & erect lasting memorials throughout cemeteries in Sydney. Our customers are normally in a period of grieving. I have attached logo files that will need to be implemented on the card. Company was established 1935. Australian Owned and Operated. Card needs to be designed to PIXO.com specification.

Target Market(s)

Our target market is based upon people that a grieving for family members that have passed away. We also deal with alot of companies that own and operate cemeteries.

Industry/Entity Type

Business

Contact Information for Business Card

Simon Harcourt, Operations Manager, 0417293086, simon@harcourtmemorials.com.au
Lewis Harcourt, Director, 0491630572, lewis@harcourtmemorials.com.au
Phone # 02 9561 3048
Website: www.harcourtmemorials.com.au
Address: Suite 17, 8 Palfrey Lane, West Carlow, Sydney NSW 2156

Font styles to use
Serif
Decorative
Script

Requirements
Must have
• Would like to see the logo nicely implemented with a modern design. Embossed lettering would be a nice additive.

```html
<!DOCTYPE html>
<html lang="en">
<head>
<meta charset="utf-8">
<title>Harcourt Memorials – Business Card</title>
<link rel="stylesheet" href="https://fonts.googleapis.com/css2?family=Open+Sans:ital,wght@0,400;0,700;1,400;1,700&display=swap">
<style>
  :root {
    --backdrop: #d9d9d9;
    --granite-light: #3a3a3a;
    --granite-mid: #2c2c2c;
    --granite-dark: #1c1c1c;
    --gold: #f2b51d;
    --white: #ffffff;
    --text-light: #ececec;
  }
  * { margin: 0; padding: 0; box-sizing: border-box; }
  html, body {
    width: 1200px;
    height: 675px;
    overflow: hidden;
    background: var(--backdrop);
  }
  .canvas {
    position: relative;
    width: 1200px;
    height: 675px;
  }
  .card {
    position: absolute;
    top: 187px;
    width: 525px;
    height: 300px;
    overflow: hidden;
    box-shadow: 0 4px 14px rgba(0,0,0,0.25);
  }
  .card--front { left: 50px; }
  .card--back { left: 625px; }
  .card__stone {
    position: absolute;
    inset: 0;
    background:
      radial-gradient(ellipse at 30% 30%, rgba(255,255,255,0.05) 0%, rgba(255,255,255,0) 60%),
      radial-gradient(ellipse at 50% 50%, var(--granite-light) 0%, var(--granite-mid) 55%, var(--granite-dark) 100%);
  }
  .card__content {
    position: absolute;
    inset: 0;
    display: flex;
    flex-direction: column;
    align-items: center;
    justify-content: center;
    text-align: center;
    font-family: "Open Sans", sans-serif;
  }
  .card--front .card__content { padding-bottom: 14px; }
  .contact__name {
    font-weight: 700;
    font-size: 23px;
    letter-spacing: 0.3px;
    color: var(--gold);
    text-transform: uppercase;
    line-height: 1.1;
  }
  .contact__role {
    font-style: italic;
    font-size: 16px;
    color: var(--white);
    margin-bottom: 10px;
  }
  .contact__address {
    font-style: italic;
    font-size: 12px;
    color: var(--text-light);
    margin-bottom: 4px;
  }
  .contact__lines {
    font-size: 12px;
    color: var(--text-light);
    margin-bottom: 2px;
    white-space: nowrap;
  }
  .contact__label {
    color: var(--gold);
    font-style: italic;
    margin-left: 6px;
  }
  .contact__label:first-child { margin-left: 0; }
  .contact__web {
    font-style: italic;
    font-weight: 700;
    font-size: 13px;
    color: var(--gold);
    margin-bottom: 10px;
  }
  .social-rule {
    display: flex;
    align-items: center;
    gap: 8px;
    width: 450px;
  }
  .social-rule__line {
    flex: 1;
    height: 1px;
    background: var(--gold);
  }
  .social-rule__dots { display: flex; gap: 5px; }
  .social-rule__dot {
    width: 11px;
    height: 11px;
    border-radius: 50%;
    background: var(--gold);
  }
  .brand {
    display: flex;
    align-items: center;
    gap: 10px;
  }
  .brand__mark {
    width: 14px;
    height: 14px;
    background: var(--white);
  }
  .brand__name {
    font-family: "Open Sans", sans-serif;
    font-weight: 700;
    font-size: 26px;
    color: var(--white);
    letter-spacing: 0.5px;
  }
</style>
</head>
<body>
<main class="canvas">
  <section class="card card--front">
    <div class="card__stone" role="img" aria-label="Black granite stone surface"></div>
    <div class="card__content">
      <h1 class="contact__name">Simon Harcourt</h1>
      <p class="contact__role">Operations Manager</p>
      <p class="contact__address">Suite 17, 8 Palfrey Lane, West Carlow, Sydney NSW 2156</p>
      <p class="contact__lines">
        <span class="contact__label">C:</span> 0417293086
        <span class="contact__label">P:</span> 02 9561 3048
        <span class="contact__label">E:</span> simon@harcourtmemorials.com.au
      </p>
      <p class="contact__web">www.harcourtmemorials.com.au</p>
      <div class="social-rule">
        <span class="social-rule__line"></span>
        <span class="social-rule__dots">
          <span class="social-rule__dot"></span>
          <span class="social-rule__dot"></span>
          <span class="social-rule__dot"></span>
          <span class="social-rule__dot"></span>
          <span class="social-rule__dot"></span>
          <span class="social-rule__dot"></span>
          <span class="social-rule__dot"></span>
          <span class="social-rule__dot"></span>
        </span>
        <span class="social-rule__line"></span>
      </div>
    </div>
  </section>

  <section class="card card--back">
    <div class="card__stone" role="img" aria-label="Black granite stone surface"></div>
    <div class="card__content">
      <div class="brand">
        <span class="brand__mark"></span>
        <p class="brand__name">Harcourt Memorials</p>
      </div>
    </div>
  </section>
</main>
</body>
</html>
```